Business Card Design - Amberfield Court

We are looking at a new design for our business cards that has a modern and professional look. We run a residential aged care facility focussing on the care of residents. The cards will be used for potential clients, consultants and business opportunities in this sector. Blue and white is our main colours and would to see these colours incorporated in the design.
Industry/Entity Type
Business
Contact Information for Business Card
Amberfield Court, Darren Walsh, dwalsh@amberfieldcourt.com.au, Finance Manager, 0472 639 208, BCom, 37 Marrabel Crescent, Brindle Vale, Qld 4093.
Look and feel
Each slider illustrates characteristics of the customer's brand and the style your logo design should communicate.

```html
<!DOCTYPE html>
<html lang="en">
<head>
<meta charset="utf-8">
<title>Amberfield Court – Business Card</title>
<link rel="stylesheet" href="https://fonts.googleapis.com/css2?family=Source+Sans+3:ital,wght@0,400;0,600;1,400&display=swap">
<style>
  :root {
    --page: #8c8d8c;
    --paper: #f4f4f4;
    --brand-blue: #426983;
    --ink: #3a3a3a;
    --muted: #7c7c7c;
    --rule: #9a9a9a;
    --white: #ffffff;
  }
  * { box-sizing: border-box; margin: 0; padding: 0; }
  html, body {
    width: 1105px; height: 1200px; overflow: hidden;
    background: var(--page);
    font-family: "Source Sans 3", "Myriad Pro", Arial, sans-serif;
  }
  .canvas { position: relative; width: 1105px; height: 1200px; }
  .card {
    position: absolute; left: 180px; width: 745px; height: 426px;
    box-shadow: 0 10px 18px rgba(0,0,0,0.35);
  }
  .card--front { top: 110px; background: var(--paper); }
  .card--back { top: 640px; background: var(--brand-blue); }

  /* front */
  .brand-name {
    position: absolute; left: 453px; top: 150px; width: 246px;
    text-align: center; white-space: nowrap;
    color: var(--brand-blue); font-weight: 600; font-size: 26px;
    letter-spacing: 0.03em; text-transform: uppercase; line-height: 1;
  }
  .holder { position: absolute; left: 37px; top: 278px; right: 37px; }
  .holder-name { color: var(--brand-blue); font-weight: 600; font-size: 26px; line-height: 1; white-space: nowrap; }
  .holder-name .credential { font-size: 19px; }
  .holder-role {
    display: flex; align-items: center; margin-top: 8px;
    color: var(--muted); font-size: 18px; white-space: nowrap;
  }
  .holder-role::after {
    content: ""; flex: 1; height: 1px; background: var(--rule); margin-left: 2px; margin-top: 4px;
  }
  .contact { position: absolute; left: 37px; top: 350px; font-size: 19px; color: var(--ink); }
  .contact-line { display: flex; align-items: center; gap: 10px; height: 29px; white-space: nowrap; }
  .contact-line svg { width: 16px; height: 16px; fill: var(--brand-blue); }
  .address {
    position: absolute; right: 37px; top: 350px; text-align: right;
    font-size: 19px; color: var(--ink); line-height: 29px; white-space: nowrap;
  }

  /* back */
  .back-name {
    position: absolute; left: 0; right: 0; top: 228px; text-align: center;
    color: var(--white); font-weight: 600; font-size: 36px; line-height: 1;
    letter-spacing: 0.03em; text-transform: uppercase; white-space: nowrap;
  }
  .back-url {
    position: absolute; left: 0; right: 0; top: 288px; text-align: center;
    color: var(--white); font-style: italic; font-size: 21px; letter-spacing: 0.06em;
  }
</style>
</head>
<body>
<main class="canvas">
  <section class="card card--front">
    <div class="brand-name">Amberfield Court</div>

    <div class="holder">
      <div class="holder-name">Darren Walsh <span class="credential">BCom</span></div>
      <div class="holder-role">Finance Manager</div>
    </div>

    <div class="contact">
      <div class="contact-line">
        <svg viewBox="0 0 16 16" aria-hidden="true"><path d="M3.6 1.2l2.3 2.6c.4.4.3 1-.1 1.4L4.6 6.3c.9 2 2.7 3.9 4.9 5l1.1-1.2c.4-.4 1-.4 1.4-.1l2.6 2.1c.4.3.5 1 .1 1.4l-1.2 1.3c-.6.6-1.6.8-2.4.4C6.3 13.3 2.8 9.8 1 5.2.7 4.4.9 3.4 1.5 2.8l1-1.5c.3-.4.8-.4 1.1-.1z"/></svg>
        <span>0472 639 208</span>
      </div>
      <div class="contact-line">
        <svg viewBox="0 0 16 16" aria-hidden="true"><path d="M1 3.5h14v9H1z"/><path d="M1.5 4l6.5 5 6.5-5" fill="none" stroke="#f4f4f4" stroke-width="1.2"/></svg>
        <span>dwalsh@amberfieldcourt.com.au</span>
      </div>
    </div>

    <div class="address">
      <div>37 Marrabel Crescent</div>
      <div>Brindle Vale, Qld 4093.</div>
    </div>
  </section>

  <section class="card card--back">
    <div class="back-name">Amberfield Court</div>
    <div class="back-url">www.amberfieldcourt.com.au</div>
  </section>
</main>
</body>
</html>
```